Fahrzeugbeschriftung für Maschinenbaufirma
Zielgruppe
Wir sind eine Maschinenbaufirma die hauptsächlich im zerspanenden Bereich (Drehen/Fräsen/Montage) für die Branchen Automobilindustrie und Medizintechnik tätig ist.
Aufgabenstellung
Design für eine LKW-Plane
- das Design ist mit einem neuem Logo (aktuell noch nicht veröffentlicht)
- schlichtes und cleanes Design, nicht zu verspielt und zu viel Grafiken
- Abmaße LKW Plane ca. 7800mm x 2050mm (wird im Digitaldruck erstellt)
- Fahrerhaus und Boardwand sind weiß
- Beispiel Tramvel mit 'altem Logo' anbei
- es handelt sich um einen Halvorn Kestel Durmax 2240 KbT mit einem Schiebeplanen-Aufbau
- Die Plane wird im Digitaltdruck erstellt und muss nicht unbedingt weiß sein (empfindlich gegen Schmutz)
- Beispielbild wie der Schiebeplanenaufbau aussieht, anbei (nur falsche Farbe)

```html
<!DOCTYPE html>
<html lang="de">
<head>
<meta charset="utf-8">
<title>Brandel Kofler GmbH – LKW-Plane</title>
<link rel="stylesheet" href="https://fonts.googleapis.com/css2?family=Barlow:wght@500;600&family=Open+Sans:wght@400&display=swap">
<style>
  :root {
    --stage: #b4b4b4;
    --tarp: #e6e8e9;
    --navy: #001c5a;
    --orange: #d96c22;
    --grey: #707378;
    --white: #ffffff;
  }
  * { margin: 0; padding: 0; box-sizing: border-box; }
  html, body {
    width: 1200px;
    height: 584px;
    overflow: hidden;
    background: var(--stage);
  }
  .tarp {
    position: absolute;
    left: 20px;
    top: 140px;
    width: 1160px;
    height: 304px;
    background: var(--tarp);
    overflow: hidden;
  }
  .brand-mark {
    position: absolute;
    left: 127px;
    top: 46px;
    width: 134px;
    height: 134px;
    border-radius: 50%;
    background: var(--navy);
  }
  .company-name {
    position: absolute;
    left: 288px;
    top: 52px;
    width: 502px;
    font-family: "Barlow", sans-serif;
    font-weight: 600;
    font-size: 64px;
    line-height: 1;
    color: var(--navy);
    letter-spacing: 1px;
    white-space: nowrap;
    text-align: center;
  }
  .legal-form {
    position: absolute;
    left: 288px;
    top: 124px;
    width: 500px;
    display: flex;
    align-items: center;
    gap: 12px;
    font-family: "Barlow", sans-serif;
    font-weight: 500;
    font-size: 33px;
    line-height: 1;
    color: var(--grey);
    letter-spacing: 1px;
  }
  .legal-form::before,
  .legal-form::after {
    content: "";
    flex: 1;
    height: 2px;
    background: var(--grey);
  }
  .band {
    position: absolute;
    left: 0;
    top: 205px;
    width: 840px;
    height: 51px;
  }
  .slogan,
  .website {
    position: absolute;
    top: 205px;
    height: 51px;
    display: flex;
    align-items: center;
    font-family: "Open Sans", sans-serif;
    font-size: 26px;
    color: var(--white);
    white-space: nowrap;
  }
  .slogan { left: 46px; }
  .website { left: 488px; }
  .corner-ring {
    position: absolute;
    left: 833px;
    top: 62px;
    width: 378px;
    height: 378px;
    border-radius: 50%;
    border: 34px solid var(--grey);
  }
</style>
</head>
<body>
  <main class="tarp">
    <div class="corner-ring" aria-hidden="true"></div>

    <div class="brand-mark" aria-hidden="true"></div>
    <h1 class="company-name">BRANDEL KOFLER</h1>
    <p class="legal-form">GMBH</p>

    <svg class="band" viewBox="0 0 840 51" aria-hidden="true">
      <polygon points="0,0 462,0 428,51 0,51" fill="var(--navy)"/>
      <polygon points="471,0 833,0 823,9 823,42 833,51 434,51" fill="var(--orange)"/>
    </svg>
    <p class="slogan">Perfect Products - Best Service</p>
    <p class="website">www.brandel-kofler.com</p>
  </main>
</body>
</html>
```